Willow Creek Gatherings Event Planning in need of a design!!

Event Planning company, does a variety of events. I like simple more rustic designs focused on almond blossoms. We are based out of Northern California, the heart of almond country. I would like to see colors in light pinks, beige, light browns, whites or creams. the final design should communicate rustic simplicity. Below are some pictures of Almond blossoms and design ideas I prefer the one called Tulip Grove. Thanks

Target Market(s)

Women in the mid twenties and older. They should be in the upper middle class in need of an amazing party design and coordinator

Industry/Entity Type

Event Planning

Contact Information for Business Card

Maren Lockwood 530-624-0295almondbaffairs@gmail.comalmondblossomaffairs.com

Font styles to use
Other font styles liked:
• Amatic SC

Requirements
Must have
• almond blossom
• my information
• simplicity
Nice to have
• rustic design
• vintage feel
• whimsical
Should not have
• i like pink but not over the top

```html
<!DOCTYPE html>
<html lang="en">
<head>
<meta charset="utf-8">
<title>Willow Creek Gatherings – Business Card</title>
<link rel="stylesheet" href="https://fonts.googleapis.com/css2?family=Jost:wght@400&family=Open+Sans:wght@400;600&display=swap">
<style>
  :root {
    --backdrop: #141414;
    --card-white: #ffffff;
    --blossom-pink: #e98fbd;
    --name-pink: #e48ab8;
    --leaf-green: #2a9a66;
    --text-grey: #555555;
    --logo-white: #ffffff;
  }
  * { margin: 0; padding: 0; box-sizing: border-box; }
  html, body { width: 1200px; height: 900px; overflow: hidden; }
  body { background: var(--backdrop); position: relative; }

  .card {
    position: absolute;
    top: 170px;
    width: 347px;
    height: 561px;
    overflow: hidden;
  }
  .card--front { left: 259px; background: var(--card-white); }
  .card--back  { left: 631px; }

  .accent-bar {
    position: absolute;
    left: 102px;
    width: 143px;
    background: var(--blossom-pink);
  }
  .accent-bar--top { top: 0; height: 30px; }
  .accent-bar--bottom { bottom: 0; height: 28px; }

  .brand-dot {
    position: absolute;
    left: 50%;
    width: 64px;
    height: 64px;
    margin-left: -32px;
    border-radius: 50%;
  }
  .card--front .brand-dot { top: 134px; background: var(--leaf-green); }
  .card--back .brand-dot { top: 372px; background: var(--logo-white); }

  .brand-name {
    position: absolute;
    left: 0; right: 0;
    text-align: center;
    font-family: "Jost", sans-serif;
    font-weight: 400;
    text-transform: uppercase;
    white-space: nowrap;
  }
  .brand-name__main { display: block; line-height: 1; }
  .brand-name__sub  { display: block; line-height: 1; }

  .card--front .brand-name { top: 218px; color: var(--blossom-pink); }
  .card--front .brand-name__main { font-size: 37px; letter-spacing: 0.5px; }
  .card--front .brand-name__sub  { font-size: 22px; letter-spacing: 2px; margin-top: 16px; }

  .person-name {
    position: absolute;
    top: 339px; left: 0; right: 0;
    text-align: center;
    font-family: "Open Sans", sans-serif;
    font-weight: 600;
    font-size: 18px;
    color: var(--name-pink);
    text-transform: uppercase;
  }

  .contact-list {
    position: absolute;
    top: 386px; left: 0; right: 0;
    list-style: none;
    font-family: "Open Sans", sans-serif;
    font-size: 14.5px;
    color: var(--text-grey);
    text-align: center;
    line-height: 20px;
  }
  .contact-list li { display: flex; justify-content: center; align-items: center; gap: 7px; }
  .contact-icon { width: 11px; height: 11px; fill: var(--blossom-pink); flex: none; }

  .orchard-photo {
    position: absolute; inset: 0;
    background:
      linear-gradient(180deg, rgba(0,0,0,0) 55%, rgba(60,55,50,0.35) 100%),
      linear-gradient(160deg, #e6e1dc 0%, #cfc8bf 25%, #a89f93 48%, #8f9a78 62%, #9a928a 78%, #aaa39b 100%);
  }
  .card--back .brand-name { top: 455px; color: var(--logo-white); }
  .card--back .brand-name__main { font-size: 41px; letter-spacing: 0.5px; }
  .card--back .brand-name__sub  { font-size: 24px; letter-spacing: 2px; margin-top: 14px; }
</style>
</head>
<body>
  <section class="card card--front">
    <div class="accent-bar accent-bar--top"></div>
    <div class="brand-dot" aria-hidden="true"></div>
    <h1 class="brand-name"><span class="brand-name__main">Willow Creek</span><span class="brand-name__sub">Gatherings</span></h1>
    <p class="person-name">Maren Lockwood</p>
    <ul class="contact-list">
      <li>
        <svg class="contact-icon" viewBox="0 0 24 24" aria-hidden="true"><path d="M6.6 10.8a15.1 15.1 0 0 0 6.6 6.6l2.2-2.2a1 1 0 0 1 1-.25 11.4 11.4 0 0 0 3.6.57 1 1 0 0 1 1 1V20a1 1 0 0 1-1 1A17 17 0 0 1 3 4a1 1 0 0 1 1-1h3.5a1 1 0 0 1 1 1c0 1.25.2 2.45.57 3.57a1 1 0 0 1-.25 1z"/></svg>
        530-817-4362
      </li>
      <li>
        <svg class="contact-icon" viewBox="0 0 24 24" aria-hidden="true"><path d="M2 5h20v14H2z"/><path d="M3 6l9 7 9-7" fill="none" stroke="#fff" stroke-width="1.8"/></svg>
        willowcgather@mailbox.test
      </li>
      <li>
        <svg class="contact-icon" viewBox="0 0 24 24" aria-hidden="true"><circle cx="12" cy="12" r="11"/><path d="M1 12h22M12 1c4 4 4 18 0 22M12 1c-4 4-4 18 0 22" fill="none" stroke="#fff" stroke-width="1.5"/></svg>
        willowcreekgatherings.test
      </li>
    </ul>
    <div class="accent-bar accent-bar--bottom"></div>
  </section>

  <section class="card card--back">
    <div class="orchard-photo" role="img" aria-label="Photo of a path running between rows of almond trees in white-pink blossom"></div>
    <div class="brand-dot" aria-hidden="true"></div>
    <h2 class="brand-name"><span class="brand-name__main">Willow Creek</span><span class="brand-name__sub">Gatherings</span></h2>
  </section>
</body>
</html>
```